Flyer-Design für psychologische Beratungspraxis für Mütter
Vielen herzlichen Dank! Super Kommunikation, alle Änderungswünsche wurden sofort umgesetzt, auch hin und her meinerseits war kein Problem, immer wieder. Schnelle Reaktion, tolle Ideen. Ich bin super zufrieden und würde jederzeit sehr gerne wieder mit brightfoxes zusammenarbeiten! Toller Flyer, ich liebe meinen neuen Flyer! :)
Zielgruppe
Gelassenheitswerkstatt ist eine psychologische Beratungspraxis. Ich unterstütze Mütter, Schwangere und Frauen mit Kinderwunsch bei Herausforderungen rund um Schwangerschaft, Geburt, Mutterschaft, und damit einhergehenden Problemen.
Aufgabenstellung
Text nochmal geringgradig geändert...siehe Datei anbei

```html
<!DOCTYPE html>
<html lang="de">
<head>
<meta charset="utf-8">
<title>Flyer – Gelassenheitswerkstatt</title>
<link href="https://fonts.googleapis.com/css2?family=Amatic+SC:wght@700&family=Inter:wght@400;600&display=swap" rel="stylesheet">
<style>
  :root{
    --navy:#27308c;
    --paper:#f7f7f5;
    --backdrop:#e4e3df;
    --pill:#dcdcdc;
    --skin:#d9b79c;
    --line:#cfcfcf;
  }
  *{margin:0;padding:0;box-sizing:border-box}
  html,body{width:1200px;height:864px;overflow:hidden}
  body{background:var(--backdrop);font-family:"Inter",Arial,sans-serif;color:var(--navy)}
  .flyer{position:absolute;left:60px;top:162px;width:1080px;height:540px;display:flex;box-shadow:0 6px 24px rgba(0,0,0,.12)}
  .page{position:relative;width:540px;height:540px;background:var(--paper);overflow:hidden}
  .page--back{border-right:1px solid var(--line)}
  .portrait{position:absolute;left:-30px;top:40px;width:230px;height:230px;border-radius:50%;
    background:radial-gradient(circle at 55% 40%,#e8cdb6 0%,var(--skin) 45%,#6b5a4e 100%)}
  .brand{position:absolute;left:270px;top:110px;display:flex;align-items:center;gap:10px;
    font-family:"Amatic SC",cursive;font-weight:700;font-size:34px;color:var(--navy)}
  .brand__dot{width:18px;height:18px;border-radius:50%;background:var(--navy)}
  .title{position:absolute;left:40px;top:290px;font-family:"Amatic SC",cursive;font-weight:700;font-size:40px;letter-spacing:.5px;color:var(--navy);white-space:nowrap}
  .contact{position:absolute;left:40px;top:355px;font-size:14px;line-height:1.35}
  .contact__name{font-weight:600}
  .contact__web{margin-top:18px}
  .contact__phone{margin-top:18px}
  .langs{position:absolute;right:36px;bottom:60px;text-align:right;font-size:14px}
  .flags{display:flex;gap:8px;justify-content:flex-end;margin-top:8px}
  .flag{width:26px;height:16px;display:block}
  .headline{position:absolute;right:50px;top:40px;display:flex;flex-direction:column;align-items:flex-end;gap:8px}
  .headline span{background:var(--pill);border-radius:20px;padding:2px 16px;font-family:"Amatic SC",cursive;font-weight:700;font-size:30px;color:var(--navy);line-height:1.15;white-space:nowrap}
  .artwork{position:absolute;left:40px;top:200px;width:500px;height:340px;
    background:linear-gradient(100deg,#f0f0ee 0%,#e8e8e6 62%,#3a429a 80%,var(--navy) 100%)}
</style>
</head>
<body>
  <div class="flyer">
    <section class="page page--back">
      <div class="portrait" role="img" aria-label="Porträtfoto der Beraterin am Schreibtisch"></div>
      <div class="brand"><span class="brand__dot"></span>Gelassenheitswerkstatt</div>
      <h2 class="title">Krisenbegleitung &amp; Lebensberatung</h2>
      <div class="contact">
        <p class="contact__name">Dr. Marlene Vasconti</p>
        <p>Systemische Beraterin (SGfB)</p>
        <p>Heilpraktikerin für Psychotherapie</p>
        <p class="contact__web">www.gelassenheitswerkstatt.de</p>
        <p>info@gelassenheitswerkstatt.de</p>
        <p class="contact__phone">0157 481 22 605</p>
      </div>
      <div class="langs">
        <p>TELEFON: 0157 481 22 605</p>
        <div class="flags">
          <svg class="flag" viewBox="0 0 3 2"><rect width="3" height=".67" fill="#000"/><rect y=".67" width="3" height=".67" fill="#d00"/><rect y="1.33" width="3" height=".67" fill="#fc0"/></svg>
          <svg class="flag" viewBox="0 0 3 2"><rect width="1" height="2" fill="#009246"/><rect x="1" width="1" height="2" fill="#fff"/><rect x="2" width="1" height="2" fill="#ce2b37"/></svg>
          <svg class="flag" viewBox="0 0 60 40"><rect width="60" height="40" fill="#012169"/><path d="M0 0L60 40M60 0L0 40" stroke="#fff" stroke-width="8"/><path d="M0 0L60 40M60 0L0 40" stroke="#c8102e" stroke-width="3"/><path d="M30 0V40M0 20H60" stroke="#fff" stroke-width="12"/><path d="M30 0V40M0 20H60" stroke="#c8102e" stroke-width="7"/></svg>
          <svg class="flag" viewBox="0 0 3 2"><rect width="1" height="2" fill="#002395"/><rect x="1" width="1" height="2" fill="#fff"/><rect x="2" width="1" height="2" fill="#ed2939"/></svg>
        </div>
      </div>
    </section>
    <section class="page page--front">
      <h1 class="headline">
        <span>Psychologische Beratungspraxis</span>
        <span>für Mütter, Schwangere</span>
        <span>und Frauen mit Kinderwunsch</span>
      </h1>
      <div class="artwork" role="img" aria-label="Linienillustration einer Mutter mit Baby im Arm und dekorative blaue Form"></div>
    </section>
  </div>
</body>
</html>
```